Business card for Crestline Bathrooms

Please design a business card for our bathroom renovation business. You can use my existing logo, but if you have an idea to modernize it, I would like to see it. Please see attached files first. I would like to use the blue and the orange theme. I like the concept of using the shower head in the logo. Please find following a design (or two) that I have been trying to create with my limited resources. That design was for a sign, but I was going to adopt it and use it as a business card as well. I like the concept of the water splash but I don’t think it “flows” nicely together with the logo. Another thought is that maybe creating the logo out of water splash could work and have a dramatic effect (like the water text and the butterfly picture attached with similar background instead of white). If the above doesn’t work I would like to see a modern simplified design. One of the attached files named as the unwanted business card has all the details that I want included in the business card. Please note that it is two sided.
Updates

I am very thankful for the designs that I have received, but they are very similar and only a couple of attempts to do something with the water splash as per my original brief. Modernizing the logo and having it made out of out of water splash with the orange as color accent could work and have a dramatic effect (like the water text and the butterfly picture attached with similar background instead of white). Please do not use the butterfly itself! This is just an example that images can be created out of water splash.

Contact Information for Business Card

all the details are on the unwonted business card file included

Colors
3176b5

Requirements
Nice to have
• Copied from the brief:
• ... maybe creating the logo out of water splash could work and have a dramatic effect (like the water text and the butterfly picture attached with similar background instead of white). Please do not use the butterfly itself!
Should not have
• I am getting designs with a butterfly. The butterfly picture was an example of creating something from a water splash. The butterfly itself has no association with anything other than the concept of creating a logo out of water splash. Sorry, I thought I was clear in the brief.

```html
<!DOCTYPE html>
<html lang="en">
<head>
<meta charset="utf-8">
<title>Crestline Bathrooms – Business Card</title>
<link rel="stylesheet" href="https://fonts.googleapis.com/css2?family=Roboto:wght@400;500&family=Roboto+Condensed:wght@400&family=Short+Stack&display=swap">
<style>
  :root {
    --bg: #e4e4e4;
    --card: #ffffff;
    --navy: #1d4e77;
    --coral: #ef7a6a;
    --brand-blue: #3176b5;
    --text: #555a60;
    --badge: #6d6f72;
    --water-light: #e6f6fd;
    --water-mid: #9fd8f3;
    --water-deep: #3d9fdc;
  }
  * { margin: 0; padding: 0; box-sizing: border-box; }
  html, body { width: 1200px; height: 960px; overflow: hidden; }
  body { background: var(--bg); position: relative; font-family: "Roboto", Arial, sans-serif; }

  .card { position: absolute; width: 600px; height: 343px; background: var(--card); overflow: hidden; }
  .card--front { left: 314px; top: 113px; }
  .card--back { left: 311px; top: 472px; }

  .brand { position: absolute; display: flex; align-items: flex-start; gap: 8px; color: var(--navy); font-family: "Roboto", Arial, sans-serif; font-weight: 500; line-height: 1; }
  .brand__dot { width: 16px; height: 16px; border-radius: 50%; background: var(--coral); margin-top: 8px; flex: none; }
  .brand__name { display: flex; flex-direction: column; }
  .brand__main { font-size: 46px; letter-spacing: -0.5px; }
  .brand__sub { font-size: 22px; letter-spacing: 4px; margin-top: 6px; padding-left: 4px; }
  .card--front .brand { left: 42px; top: 62px; }
  .card--back .brand { left: 384px; top: 50px; }

  .holder { position: absolute; left: 42px; top: 243px; font-family: "Short Stack", "Comic Sans MS", cursive; font-size: 24px; color: var(--navy); }

  .contact { position: absolute; left: 322px; top: 184px; list-style: none; font-size: 14.5px; color: var(--text); }
  .contact li { display: flex; align-items: flex-start; gap: 9px; line-height: 19px; }
  .contact li + li { margin-top: 0; }
  .contact .contact__address { margin-bottom: 9px; }
  .contact svg { width: 13px; height: 13px; margin-top: 3px; fill: var(--navy); flex: none; }

  .memberships { position: absolute; left: 40px; top: 44px; display: flex; align-items: center; gap: 12px; }
  .memberships__badge { width: 30px; height: 34px; border-radius: 6px; background: var(--badge); }
  .memberships__divider { width: 1px; height: 34px; background: var(--badge); }
  .memberships__badge--wide { width: 116px; height: 22px; border-radius: 3px; }

  .services { position: absolute; left: 41px; top: 95px; list-style: none; font-family: "Roboto Condensed", "Arial Narrow", sans-serif; font-size: 14.5px; color: var(--text); }
  .services li { line-height: 19px; display: flex; align-items: center; gap: 7px; }
  .services li::before { content: ""; width: 5px; height: 5px; border-radius: 50%; background: var(--navy); }

  .water { position: absolute; left: 0; bottom: 0; width: 600px; height: 200px;
    background:
      linear-gradient(180deg, rgba(255,255,255,0) 0%, var(--water-light) 40%, var(--water-mid) 72%, var(--water-deep) 88%, var(--water-mid) 100%); }
</style>
</head>
<body>

  <section class="card card--front" aria-label="Business card front">
    <div class="brand">
      <span class="brand__dot"></span>
      <span class="brand__name"><span class="brand__main">Crestline</span><span class="brand__sub">Bathrooms</span></span>
    </div>

    <p class="holder">Daniel Mercer</p>

    <ul class="contact">
      <li class="contact__address">
        <svg viewBox="0 0 16 16"><path d="M8 0a5.5 5.5 0 0 0-5.5 5.5C2.5 10 8 16 8 16s5.5-6 5.5-10.5A5.5 5.5 0 0 0 8 0zm0 8a2.5 2.5 0 1 1 0-5 2.5 2.5 0 0 1 0 5z"/></svg>
        <span>PO Box 41<br>Harwood Vale 2710</span>
      </li>
      <li>
        <svg viewBox="0 0 16 16"><path d="M3.5 1l2.4 3-1.4 1.8c.9 2 2.5 3.6 4.5 4.6l1.8-1.4 3 2.4-1.3 2.9C7 14.200 1.800 9 1.100 2.300z"/></svg>
        <span>0400 555 218</span>
      </li>
      <li>
        <svg viewBox="0 0 16 16"><path d="M4 0h8a1 1 0 0 1 1 1v14a1 1 0 0 1-1 1H4a1 1 0 0 1-1-1V1a1 1 0 0 1 1-1zm1 2v10h6V2H5zm3 11a1 1 0 1 0 0 2 1 1 0 0 0 0-2z"/></svg>
        <span>6200 5519</span>
      </li>
      <li>
        <svg viewBox="0 0 16 16"><path d="M1 4h14v9H1z M1 4l7 5 7-5" fill="none" stroke="#1d4e77" stroke-width="1.6"/></svg>
        <span>daniel@crestlinebathrooms.com.au</span>
      </li>
      <li>
        <svg viewBox="0 0 16 16"><circle cx="8" cy="8" r="6.5" fill="none" stroke="#1d4e77" stroke-width="1.6"/><path d="M1.5 8h13M8 1.5c-3 3.5-3 9.5 0 13M8 1.5c3 3.5 3 9.5 0 13" fill="none" stroke="#1d4e77" stroke-width="1.2"/></svg>
        <span>crestlinebathrooms.com.au</span>
      </li>
    </ul>
  </section>

  <section class="card card--back" aria-label="Business card back">
    <div class="water" role="img" aria-label="Blue water splash wave with droplets along the bottom of the card"></div>

    <div class="memberships" aria-label="Industry memberships">
      <span class="memberships__badge"></span>
      <span class="memberships__divider"></span>
      <span class="memberships__badge memberships__badge--wide"></span>
    </div>

    <ul class="services">
      <li>Complete Bathroom Renovations &amp; Remodelling</li>
      <li>Highly Skilled &amp; Qualified Tradespeople</li>
      <li>Professional Service From Concept To Completion</li>
      <li>All Work Guaranteed</li>
    </ul>

    <div class="brand">
      <span class="brand__dot"></span>
      <span class="brand__name"><span class="brand__main">Crestline</span><span class="brand__sub">Bathrooms</span></span>
    </div>
  </section>

</body>
</html>
```